Attorney Website Home Page Design Project

I am starting my law firm and I need a website design. I am going to be practicing in the field of personal injury, and I need a website design that conveys reliability and professionalism, but is still personable. This website will mostly be accessed by potential clients looking for information about me, and my potential clients are individual people, not businesses.

I have a logo that I just had designed by a designer on this site that I will be using. The colors used int he site should be complementary to the ones in that logo. Also, I have listed three websites that I want to base the overall look of my site on. This does NOT mean I want to copy them- instead, I am listing them for inspiration and to better convey what I am looking for.

Please use filler text and filler images for everything, and structure the menus as I have described below.

I will be taking this design- as a PSD file- and having it converted in to HTML, so I will need a perfect, multi-layered PSD file when completed.

I also will need a contact form that is consistent on every page.

Overall design on this site is up to you. See the attached logo files for inspiration on the color scheme. I am looking for a professional but personal website for my law firm. Check out the sites below for inspiration.

I. Websites for inspiration:

www.DonovanKemptLaw.com THIS IS WHERE I WANT ABOUT 50% OF YOUR INSPIRATION TO COME FROM

www.OkaforPersonalInjury.com 25%

www.VelmorAdvocate.com 25%

I want all aspects of this site- menu panels and what not to be expandable and done in full uncompressed photoshop psd format so I can have them converted to html, and then in to a full site.

See the attached logo- the colors in it should direct the overall color scheme of the site.

I want you to use placeholder text and placeholder images- you can use white boxes with text in them that says what type of image should be used in its place. I also want a placeholder for a video on the home page.

II. Menu structure:

A. Main Menu and Submenu Items:

Our Purpose

What An Attorney Does

Why Choose Quillbrook Attorneys

No Fee Guarantee

Cases We Handle (Below is a partial list- take the whole list from DonovanKemptLaw.com

Auto Accidents

Slip and Fall Injuries

Dog Bites

Animal Bites

General Injury Cases

Your Case

How Are You Feeling?

What You Should Be Doing

Talk To Us

Contact Us

Target Market(s)

Injured people who need an attorney. Individuals, not companies.

Industry/Entity Type

Law Firm

Requirements
Must have
• Must be themed according to the websites I have listed and in line with my logo.

Must convey reliability, professionalism and warmth.

Must appeal to an individual person- I am practicing personal injury, not corporate or business law.

Must have one eye-catching item- "Contact Us Now to Get These Questions Answered:" with a 10 item numbered list of questions.
Should not have
• The site should not be cluttered or difficult to follow.

It should not be elitist or look like it is designed for corporate law.

```html
<!DOCTYPE html>
<html lang="en">
<head>
<meta charset="utf-8">
<title>Quillbrook Attorneys – Home</title>
<link href="https://fonts.googleapis.com/css2?family=Open+Sans:wght@400;600&family=PT+Serif:wght@400;700&family=Arimo:wght@400;700&display=swap" rel="stylesheet">
<style>
:root{
  --navy:#1b4a7e;
  --navy-dark:#0d3763;
  --blue:#1f6fb0;
  --link:#2a8fd0;
  --cyan:#1aa3dc;
  --orange:#e2682a;
  --text:#555;
  --heading:#3a3a3a;
  --hero:#e4e5e8;
  --footer:#2b2b2b;
  --footer-text:#b9b9b9;
  --white:#fff;
}
*{margin:0;padding:0;box-sizing:border-box}
html,body{width:987px;height:1200px;overflow:hidden;background:var(--white)}
body{position:relative;font-family:"Arimo",Arial,sans-serif;color:var(--text);font-size:10px}
.abs{position:absolute}

/* header */
.site-header{left:0;top:0;width:987px;height:82px;background:var(--white)}
.brand{left:172px;top:20px;text-align:center;width:250px}
.brand-name{font-family:"Open Sans",sans-serif;font-weight:600;color:var(--navy);font-size:27px;letter-spacing:1px;line-height:30px;white-space:nowrap}
.phone-box{left:528px;top:0;width:300px;height:78px;background:linear-gradient(#f3f3f3,#dcdcdc);border:1px solid #cfcfcf;text-align:center;font-family:"PT Serif",serif}
.phone-box .call{font-size:16px;color:#333;margin-top:4px}
.phone-box .number{font-size:40px;font-weight:700;color:var(--blue);line-height:44px}

/* hero */
.hero{left:0;top:82px;width:987px;height:379px;background:linear-gradient(#eceef1,var(--hero))}
.hero-photo{left:165px;top:10px;width:315px;height:369px;border-radius:150px 150px 0 0;background:linear-gradient(#d9b497,#c99e7f 45%,#2a2a30 75%)}
.main-nav{left:420px;top:95px;width:414px;height:39px;background:linear-gradient(#2a6aa8,var(--navy-dark));border-radius:4px;display:flex;align-items:center;font-family:"Open Sans",sans-serif;font-size:11px;color:var(--white)}
.main-nav span{padding:0 10px;border-right:1px solid #0a2c50;line-height:39px}
.main-nav .lang{flex:1;margin-left:4px;background:#0f3d6c;height:30px;line-height:30px;border-radius:3px;margin-right:6px;display:flex;align-items:center;padding:0 8px;border:none}
.flag{width:16px;height:10px;background:#c8283a;margin-right:10px;border:2px solid #1e3a8a}
.contact-panel{left:609px;top:140px;width:213px;height:270px;background:#c9ccd1;border-radius:6px;padding:6px}
.contact-inner{width:100%;height:100%;background:linear-gradient(160deg,#1f5e9c,var(--navy-dark));border-radius:3px;position:relative}
.contact-inner h2{font-family:"Open Sans",sans-serif;font-weight:600;color:var(--white);font-size:20px;text-align:center;padding-top:12px}
.field{position:absolute;left:9px;width:182px;background:var(--white);border-radius:3px;font-size:7px;color:#aaa;padding:7px 8px}
.field.select::after{content:"";position:absolute;right:4px;top:3px;width:14px;height:14px;background:#7fb0db;border-radius:2px}
.send-btn{position:absolute;right:14px;bottom:12px;background:linear-gradient(#fff,#ddd);border-radius:3px;font-size:9px;font-weight:700;color:#333;padding:4px 7px}
.thumbs{left:586px;top:421px;display:flex;gap:5px}
.thumbs div{width:44px;height:31px;border:2px solid var(--white);box-shadow:0 0 2px #999}

/* content */
.col h3{font-family:"Open Sans",sans-serif;font-weight:400;font-size:19px;color:var(--heading)}
.col p{font-size:9.5px;line-height:16.5px}
.img-box{border:3px solid var(--white);box-shadow:0 0 3px #aaa}
.btn{background:linear-gradient(#2b74b7,var(--navy-dark));color:var(--white);font-size:10px;font-weight:700;border-radius:3px;padding:6px 8px;display:inline-block}
.practice{display:flex;gap:10px;padding-bottom:8px;margin-bottom:10px;border-bottom:1px solid #ddd;width:222px}
.practice .thumb{width:60px;height:55px;flex:none}
.practice b{display:block;color:var(--link);font-weight:400;font-size:11px;margin-bottom:2px}
.practice p{font-size:9px;line-height:14px}
.info-strip{left:162px;top:790px;width:663px;height:111px;border:1px solid #ddd;border-radius:4px;display:flex}
.info-strip div{flex:1;padding:8px 20px;border-right:1px solid #e6e6e6}
.info-strip div:last-child{border:none}
.info-strip h4{font-family:"Open Sans",sans-serif;font-weight:400;font-size:16px;color:var(--heading);margin-bottom:6px}
.info-strip h4.accent{color:var(--cyan)}
.info-strip p{font-size:9px;line-height:13px;text-align:justify}
.info-strip .more{display:block;text-align:right;color:var(--orange);font-size:9px;margin-top:6px;padding-right:10px}
.questions-promo{left:843px;top:762px;width:144px;height:158px}
.questions-promo .title{color:var(--link);font-size:11px;text-align:center;line-height:14px}
.promo-art{position:absolute;left:40px;top:44px;width:104px;height:114px;background:linear-gradient(#c9a98d,#3a3a3a)}
.click-btn{position:absolute;left:-6px;top:128px;width:110px;height:25px;background:linear-gradient(#2c8ed0,#0f5596);border-radius:4px;color:var(--white);font-family:"Open Sans",sans-serif;font-size:14px;text-align:center;line-height:25px}

/* footer */
.site-footer{left:0;top:920px;width:987px;height:280px;background:var(--footer);color:var(--footer-text)}
.site-footer h3{font-family:"Open Sans",sans-serif;font-weight:400;font-size:16px;color:var(--white)}
.member{display:flex;gap:14px;margin-top:14px}
.badge{width:52px;height:52px;flex:none;border:3px solid var(--white);background:#7a1e14}
.member p{font-size:9px;line-height:16.5px;text-align:justify;color:var(--footer-text)}
.member .btn{float:right;margin-top:-2px}
.office p{font-size:9px;line-height:16px;color:#ddd}
.office .row{display:flex;justify-content:space-between;width:162px}
.social li{list-style:none;display:flex;align-items:center;gap:18px;height:33px;font-size:10px;color:#ccc}
.social i{width:28px;height:28px;border-radius:4px;display:block}
.legal{right:130px;top:1164px;text-align:right;font-size:9px;color:#999;line-height:14px}
</style>
</head>
<body>

<header class="site-header abs">
  <div class="brand abs"><div class="brand-name">QUILLBROOK ATTORNEYS</div></div>
  <div class="phone-box abs">
    <div class="call">Call for a FREE CONSULTATION</div>
    <div class="number">(800)555-0142</div>
  </div>
</header>

<section class="hero abs">
  <div class="hero-photo abs" role="img" aria-label="Portrait photo of a smiling attorney"></div>
</section>

<nav class="main-nav abs">
  <span>Our Story</span><span>Your Stories</span><span>Our Services</span><span>Your Case</span>
  <span class="lang"><i class="flag"></i>English
    <svg width="8" height="6" style="margin-left:auto" viewBox="0 0 8 6"><path d="M1 1l3 3 3-3" stroke="#fff" fill="none" stroke-width="1.5"/></svg>
  </span>
</nav>

<aside class="contact-panel abs">
  <div class="contact-inner">
    <h2>Contact Us Now</h2>
    <div class="field" style="top:55px">type your name in here</div>
    <div class="field select" style="top:92px">select your area of enquiry</div>
    <div class="field" style="top:128px;height:106px">type your message here...</div>
    <div class="send-btn">Learn More</div>
  </div>
</aside>

<div class="thumbs abs">
  <div role="img" aria-label="Attorney portrait thumbnail" style="background:#d8c3b0"></div>
  <div role="img" aria-label="Attorney portrait thumbnail" style="background:#6b6f78"></div>
  <div role="img" aria-label="Gavel thumbnail" style="background:#8a5a3c"></div>
  <div role="img" aria-label="Attorney portrait thumbnail" style="background:#9a8b80"></div>
  <div role="img" aria-label="Attorney portrait thumbnail" style="background:#b59d8c"></div>
</div>

<section class="col abs" style="left:162px;top:482px;width:205px">
  <h3>Welcome to our site</h3>
  <div class="img-box" role="img" aria-label="Gavel and scales of justice on books" style="margin-top:12px;width:201px;height:76px;background:linear-gradient(90deg,#4a3020,#a77a4e,#5a3a22)"></div>
  <p style="margin-top:10px">Lorem ipsum dolor sit amet, consectetur adipiscing elit. Fusce accumsan, elit a suscipit sagittis, tortor sapien cursus risus, non rhoncus lectus nunc ac nulla.<br>Aliquam molestie, mi et imperdiet euismod, dui purus auctor tellus, et interdum lacus lectus et ante. Sed accumsan sollicitudin sapien, sit amet adipiscing turpis gravida ac.</p>
  <span class="btn" style="margin-top:14px">Learn More</span>
</section>

<section class="col abs" style="left:387px;top:482px;width:225px">
  <h3>Practice Areas</h3>
  <div style="margin-top:12px">
    <div class="practice"><div class="thumb img-box" role="img" aria-label="Aircraft accident scene" style="background:#9aa0a6"></div><div><b>Aircraft Accident</b><p>Lorem ipsum dolor sit amet, consectetur adipiscing elit.</p></div></div>
    <div class="practice"><div class="thumb img-box" role="img" aria-label="Damaged red car" style="background:#b8453c"></div><div><b>Auto Accident</b><p>Lorem ipsum dolor sit amet, consectetur adipiscing elit.</p></div></div>
    <div class="practice" style="border:none"><div class="thumb img-box" role="img" aria-label="Dog bite injury" style="background:#5d5a3a"></div><div><b>Dog Bite Injury</b><p>Lorem ipsum dolor sit amet, consectetur adipiscing elit.</p></div></div>
  </div>
  <span class="btn" style="margin-top:4px">Learn More</span>
</section>

<section class="col abs" style="left:614px;top:482px;width:214px">
  <h3>Watch Our Video</h3>
  <div style="margin-top:16px;width:214px;height:122px;background:#222;position:relative;border:1px solid #111">
    <div role="img" aria-label="Video still of an attorney in an office" style="position:absolute;inset:0 0 14px 0;background:linear-gradient(90deg,#4a3a2e,#7a6a5c,#3a3a3a)"></div>
    <svg class="abs" style="left:94px;top:45px" width="26" height="18" viewBox="0 0 26 18"><rect width="26" height="18" rx="3" fill="#111" opacity=".8"/><path d="M10 5l7 4-7 4z" fill="#fff"/></svg>
    <div style="position:absolute;left:0;right:0;bottom:12px;height:3px;background:#c22"></div>
    <div style="position:absolute;left:0;right:0;bottom:0;height:12px;background:#1a1a1a"></div>
  </div>
  <p style="margin-top:14px;text-align:justify">Sed ut perspiciatis unde omnis iste natus error sit voluptatem accusantium doloremque laudan tium, totam rem aperiam, eaque ipsa quae ab illo inventore veritatis et quasi architecto beatae vitae dicta sunt explicabo. Nemo enim ipsam voluptatem quia voluptas.</p>
</section>

<section class="info-strip abs">
  <div><h4 class="accent">Our Purpose</h4><p>Lorem Ipsum is simply dummy text of the printing and typesetting industry. Lorem Ipsum has been the industry's standard dummy text</p><span class="more">Read More &gt;&gt;</span></div>
  <div><h4>What an Attorney Does</h4><p>Lorem Ipsum is simply dummy text of the printing and typesetting industry. Lorem Ipsum has been the industry's standard dummy text</p><span class="more">Read More &gt;&gt;</span></div>
  <div><h4>Why Choose Us</h4><p>Lorem Ipsum is simply dummy text of the printing and typesetting industry. Lorem Ipsum has been the industry's standard dummy text</p><span class="more">Read More &gt;&gt;</span></div>
</section>

<aside class="questions-promo abs">
  <div class="title">Top 10 Questions<br>We Are Asked<br>By Injured People</div>
  <div class="promo-art" role="img" aria-label="Illustration of a thoughtful man with speech bubbles"></div>
  <div class="click-btn">CLICK HERE</div>
</aside>

<footer class="site-footer abs">
  <div class="abs" style="left:162px;top:30px;width:268px">
    <h3>Membership &amp; Accreditation
      <svg style="margin-left:62px" width="30" height="12" viewBox="0 0 30 12"><path d="M6 1L1 6l5 5M24 1l5 5-5 5" stroke="#888" fill="none" stroke-width="1.6"/></svg>
    </h3>
    <div class="member"><div class="badge" role="img" aria-label="Accreditation badge"></div><div><p>Lorem ipsum dolor sit amet, consectetur adipiscing elit. Fusce accumsan, elit a suscipit sagittis, tortor sapien cursus risus, non rhoncus lectus nunc ac nulla.</p><span class="btn">Learn More</span></div></div>
    <div class="member" style="margin-top:18px"><div class="badge" role="img" aria-label="Accreditation badge"></div><div><p>Lorem ipsum dolor sit amet, consectetur adipiscing elit. Fusce accumsan, elit a suscipit sagittis, tortor sapien cursus risus, non rhoncus lectus nunc ac nulla.</p><span class="btn">Learn More</span></div></div>
  </div>

  <div class="office abs" style="left:474px;top:22px;width:180px">
    <h3>Main Office</h3>
    <div style="font-family:'Open Sans',sans-serif;font-weight:600;color:#9a9a9a;font-size:14px;margin:10px 0 4px">QUILLBROOK</div>
    <p>4120 Ashdale<br>Road,Glasgow, D07 41KT.</p>
    <p class="row" style="margin-top:8px"><span>Toll - Free:</span><span>+1 800 xxx xxxx</span></p>
    <p class="row" style="margin-top:4px"><span>Telephone:</span><span>+1 800 xxx xxxx</span></p>
    <p style="margin-top:4px">Email : <span style="color:var(--link)">mailto@quillbrook.com</span></p>
    <p style="margin-top:12px;font-weight:700;font-size:11px;color:var(--white)">Office Hours:</p>
    <p style="margin-top:4px">8:30 a.m. to 5:30 p.m.</p>
    <p style="margin-top:4px">(Pacific), M-F</p>
  </div>

  <div class="abs" style="left:679px;top:22px;width:150px">
    <h3>Connect with Us</h3>
    <ul class="social" style="margin-top:10px">
      <li><i style="background:#3ea6d9"></i>Chirpline</li>
      <li><i style="background:#3b5998"></i>Linkhall</li>
      <li><i style="background:#444"></i>Circleplus</li>
      <li><i style="background:#e9e9e9"></i>Clipstream</li>
    </ul>
  </div>
</footer>

<div class="legal abs">Copyright © 2012,Quillbrook.<br>All Rights Reserved. | Legal &nbsp;| &nbsp;Privacy Policy</div>

</body>
</html>
```